Website Design for a holiday home letting busines

We require a redesign of our present website www.pinebrookstays.com. We want the website to stand out and look professional and clean to make holiday hunters want to book a caravan or lodge holiday with us. Our logo is red however we DO NOT want the website to be red. We want a natural colour scheme.

The final design should communicate that we are a professional company to book with.

On the home page we require;
Overview of company
Photo
Search box for holiday (check in)
Late Deals
Reviews
News

We would like the following pages designed; home page, available dates page, caravans page, content page.

The website should be responsive for smart phones. One website I do like is http://www.verdoliso.be/nl/

Target Market(s)

Families

Industry/Entity Type

Travel

Number of Pages Required

5+ page

Font styles to use
Serif

Requirements
Must have
• The project must be responsive for mobile phones and tablets.
• Ability to search for holiday home holidays
• We want a natural colour scheme.
Nice to have
• A style we like is http://www.verdoliso.be/nl/
Should not have
• Do not use red as a colour for the website. Our logo is red so this is the only time we want this used.

```html
<!DOCTYPE html>
<html lang="en">
<head>
<meta charset="utf-8">
<title>Kestrel Bay Entertainment and Activities – Pinebrook Stays</title>
<link rel="stylesheet" href="https://fonts.googleapis.com/css2?family=PT+Serif:wght@400;700&display=swap">
<style>
:root{
  --teal:#2b8f93;
  --teal-dark:#1f6f73;
  --navy:#1c4556;
  --navy-deep:#15333f;
  --brand-red:#c8312a;
  --cta:#6f8f3a;
  --cta-dark:#5a7630;
  --yellow:#f2c12e;
  --text:#5b6468;
  --heading:#2b8f93;
  --line:#e2e6e7;
  --sky-top:#cfe4ee;
  --sky-bottom:#ffffff;
}
*{box-sizing:border-box;margin:0;padding:0}
html,body{width:1200px;height:2584px;overflow:hidden}
body{font-family:"PT Serif",Georgia,serif;color:var(--text);background:#fff;position:relative}

.hero-band{position:absolute;left:0;top:0;width:1200px;height:160px;
  background:linear-gradient(180deg,var(--sky-top),var(--sky-bottom))}

.site-header{position:absolute;left:0;top:0;width:1200px;height:92px}
.brand{position:absolute;left:50px;top:26px;display:flex;align-items:center;gap:10px}
.brand-mark{width:30px;height:30px;background:var(--brand-red);border-radius:50%}
.brand-name{font-size:24px;font-weight:700;color:var(--brand-red)}
.enquiry{position:absolute;right:260px;top:22px;text-align:right}
.enquiry-label{font-size:10px;font-weight:700;letter-spacing:.5px;color:var(--navy)}
.enquiry-phone{font-size:17px;font-weight:700;color:var(--navy)}
.ask-button{position:absolute;right:50px;top:16px;width:190px;height:50px;border-radius:6px;
  background:var(--cta);color:#fff;display:flex;align-items:center;gap:10px;padding-left:12px}
.ask-icon{width:30px;height:30px;border-radius:50%;background:#fff;color:var(--cta-dark);
  font-weight:700;font-size:18px;display:flex;align-items:center;justify-content:center}
.ask-text strong{display:block;font-size:16px;line-height:1.1}
.ask-text span{font-size:11px}

.main-nav{position:absolute;left:50px;top:96px;width:1100px;height:36px;background:#fff;
  border:1px solid var(--line);display:flex}
.main-nav a{font-size:11px;font-weight:700;color:var(--navy);text-decoration:none;
  padding:0 16px;display:flex;align-items:center;text-transform:uppercase}
.main-nav a.active{background:var(--teal);color:#fff}

.page-intro{position:absolute;left:70px;top:160px;width:1060px}
.page-title{font-size:20px;font-weight:700;color:var(--heading);text-transform:uppercase;letter-spacing:.3px}
.page-intro p{font-size:12px;line-height:1.55;margin-top:6px}

.activities{position:absolute;left:70px;top:264px;width:1060px;
  display:grid;grid-template-columns:repeat(4,244px);column-gap:28px;grid-auto-rows:392px}
.activity{text-align:center}
.activity-photo{width:244px;height:190px;border:3px solid #fff;box-shadow:0 0 0 1px var(--line)}
.activity h2{font-size:13px;font-weight:700;color:var(--heading);text-transform:uppercase;
  margin:16px 0 10px;line-height:1.3}
.activity p{font-size:12px;line-height:1.6;padding:0 6px}

.site-footer{position:absolute;left:0;top:2232px;width:1200px;height:312px;background:var(--navy);color:#d7e3e7}
.footer-col{position:absolute;top:40px}
.footer-col h3{font-size:20px;font-weight:700;color:#fff;text-transform:uppercase;margin-bottom:18px}
.footer-col p{font-size:12px;line-height:1.6}
.newsletter{left:50px;width:330px}
.field{width:240px;height:32px;background:#fff;margin-top:12px;border-radius:2px;
  font-size:11px;color:#9aa3a6;padding:8px 10px}
.subscribe{display:inline-block;margin-top:14px;background:var(--yellow);color:var(--navy-deep);
  font-size:12px;font-weight:700;padding:9px 22px;text-transform:uppercase}
.contact{left:440px;width:330px}
.contact-line{display:flex;align-items:center;gap:10px;margin-top:12px;font-size:12px}
.sitemap{left:840px;width:320px}
.sitemap-lists{display:flex;gap:80px}
.sitemap ul{list-style:none}
.sitemap li{font-size:12px;line-height:2.1}

.bottom-bar{position:absolute;left:0;top:2544px;width:1200px;height:40px;background:var(--navy-deep);
  color:#9fb4bb;font-size:11px;display:flex;align-items:center;justify-content:space-between;padding:0 50px}
.social{display:flex;align-items:center;gap:8px}
.social i{width:18px;height:18px;border-radius:50%;background:#5f7e89;display:block}
</style>
</head>
<body>

<div class="hero-band" role="img" aria-label="Faded photograph of holiday lodges and caravans under a pale sky"></div>

<header class="site-header">
  <div class="brand"><span class="brand-mark"></span><span class="brand-name">Pinebrook Stays</span></div>
  <div class="enquiry">
    <div class="enquiry-label">GENERAL ENQUIRY</div>
    <div class="enquiry-phone">0800 555 0142</div>
  </div>
  <div class="ask-button">
    <span class="ask-icon">?</span>
    <span class="ask-text"><strong>Questions?</strong><span>Ask us here</span></span>
  </div>
</header>

<nav class="main-nav">
  <a>Home</a><a>About</a><a>Reviews</a><a class="active">Caravans &amp; Lodges</a>
  <a>Forward Tours</a><a>Kestrel Bay</a><a>Late Deals</a><a>News</a><a>Contact Us</a>
</nav>

<section class="page-intro">
  <h1 class="page-title">Kestrel Bay Entertainment and Activities</h1>
  <p>Kestrel Bay Holiday Park on the Northumberland coast is one of the finest parks in the region, with plenty of things to do for all the family. Whether you are looking for evening entertainment, activities for the children or a relaxing break, the park has something for everyone. Entertainment runs from early spring through to the end of the autumn season, and our lodges and caravans sit close to every facility.</p>
</section>

<section class="activities">
  <article class="activity"><div class="activity-photo" role="img" aria-label="Photo of a stage show with colourful lights" style="background:linear-gradient(135deg,#6a3fa0,#d0508a)"></div>
    <h2>Live Evening Entertainment</h2><p>Each evening the lively showbar fills with music, comedy, dancing and family shows, with something new on stage every night of your stay.</p></article>
  <article class="activity"><div class="activity-photo" role="img" aria-label="Photo of children at a kids club" style="background:linear-gradient(135deg,#f2b441,#e46c3a)"></div>
    <h2>Kids Clubs</h2><p>Our clubs offer crafts, games and outdoor fun for every age group, run by friendly staff so younger guests never run short of things to do.</p></article>
  <article class="activity"><div class="activity-photo" role="img" aria-label="Photo of an indoor heated swimming pool with slides" style="background:linear-gradient(135deg,#3fb0d9,#1d7fa8)"></div>
    <h2>Two Indoor Heated Swimming Pools</h2><p>Splash in two heated indoor pools with slides, flumes and a shallow lagoon for little ones, open from morning until early evening.</p></article>
  <article class="activity"><div class="activity-photo" role="img" aria-label="Photo of a restaurant dining room" style="background:linear-gradient(135deg,#c8874a,#7a4a2a)"></div>
    <h2>Plenty to Eat and Drink</h2><p>Choose from a family restaurant, a coffee shop, a takeaway and a bar serving hearty meals, fresh snacks and treats throughout the day.</p></article>

  <article class="activity"><div class="activity-photo" role="img" aria-label="Photo of horse riding through green fields" style="background:linear-gradient(135deg,#8fb35a,#4f7a35)"></div>
    <h2>Horse Riding</h2><p>Gentle rides for beginners and longer hacks for confident riders head out along quiet lanes and open fields near the park.</p></article>
  <article class="activity"><div class="activity-photo" role="img" aria-label="Photo of a supermarket aisle" style="background:linear-gradient(135deg,#e0d2b0,#a8906a)"></div>
    <h2>Village Supermarket</h2><p>The on-site village store stocks fresh bread, groceries, drinks and holiday essentials, so there is no need to leave the park.</p></article>
  <article class="activity"><div class="activity-photo" role="img" aria-label="Photo of a tennis court" style="background:linear-gradient(135deg,#4fa35a,#2e7a3e)"></div>
    <h2>Tennis Courts</h2><p>Book a court at reception and enjoy a friendly match on well kept surfaces, with rackets and balls available to hire.</p></article>
  <article class="activity"><div class="activity-photo" role="img" aria-label="Photo of pool games and inflatables" style="background:linear-gradient(135deg,#f0a13c,#3aa7c8)"></div>
    <h2>Pool Activities</h2><p>Try aqua games, swim lessons and inflatable sessions run by qualified lifeguards during the busy holiday weeks.</p></article>

  <article class="activity"><div class="activity-photo" role="img" aria-label="Photo of a sandy beach and sea" style="background:linear-gradient(180deg,#9cc8e0,#e0cf9c)"></div>
    <h2>The Beach</h2><p>A short stroll brings you to wide sandy beaches, rock pools and coastal paths perfect for picnics and peaceful afternoons.</p></article>
  <article class="activity"><div class="activity-photo" role="img" aria-label="Photo of a golf course green" style="background:linear-gradient(180deg,#a7cfe6,#5f9e48)"></div>
    <h2>9-Hole Golf Course</h2><p>Our nine hole course suits players of every level, with clubs to hire and a relaxed pace for family rounds.</p></article>
  <article class="activity"><div class="activity-photo" role="img" aria-label="Photo of outdoor sports activities" style="background:linear-gradient(135deg,#d6a24a,#6f9a4a)"></div>
    <h2>Sporting Activities</h2><p>From archery and football to fencing and climbing, there are plenty of ways to stay active throughout your holiday.</p></article>
  <article class="activity"><div class="activity-photo" role="img" aria-label="Photo of a costumed character at breakfast" style="background:linear-gradient(135deg,#e8b84a,#c45a3a)"></div>
    <h2>Character Breakfasts</h2><p>Start the day with a special breakfast where your little ones can meet favourite characters and collect a photo memory.</p></article>

  <article class="activity"><div class="activity-photo" role="img" aria-label="Photo of a pub restaurant interior" style="background:linear-gradient(135deg,#9a6a3e,#4a3222)"></div>
    <h2>Cask and Kettle Pub Restaurant</h2><p>Relax in our pub restaurant with classic dishes, local ales and a warm welcome, plus a garden terrace for sunny evenings.</p></article>
  <article class="activity"><div class="activity-photo" role="img" aria-label="Photo of a lounge showbar stage" style="background:linear-gradient(135deg,#3a4a8a,#a0508a)"></div>
    <h2>Live Lounge Showbar</h2><p>The live lounge hosts tribute acts, bingo and family discos, with comfortable seating and a bar close to the stage.</p></article>
  <article class="activity"><div class="activity-photo" role="img" aria-label="Photo of a coastal walking path" style="background:linear-gradient(180deg,#b5d3e3,#7ea35a)"></div>
    <h2>Scenic Walks</h2><p>Marked trails lead through woodland, meadows and along the shoreline, showing off the wildlife and views of the coast.</p></article>
  <article class="activity"><div class="activity-photo" role="img" aria-label="Photo of an amusement arcade" style="background:linear-gradient(135deg,#d24a6a,#f0b03a)"></div>
    <h2>Amusements</h2><p>The amusement arcade keeps the whole family entertained with classic games, prize machines and rides for younger children.</p></article>

  <article class="activity"><div class="activity-photo" role="img" aria-label="Photo of a boating lake with pedalos" style="background:linear-gradient(180deg,#a8cfe2,#4d8fa8)"></div>
    <h2>Boating Lake</h2><p>Hire a pedalo or rowing boat on the tranquil lake and spend a calm hour drifting past reeds and resting swans.</p></article>
  <article class="activity"><div class="activity-photo" role="img" aria-label="Photo of ducks at the lakeside" style="background:linear-gradient(180deg,#8fbcd0,#6e9250)"></div>
    <h2>Feed the Ducks</h2><p>Bring a bag of grain and visit the lakeside, where friendly ducks and geese gather along the water's edge every day.</p></article>
  <article class="activity"><div class="activity-photo" role="img" aria-label="Photo of a children's play area" style="background:linear-gradient(135deg,#e86a3a,#5aa04a)"></div>
    <h2>Play Areas</h2><p>Safe, fenced play areas with swings, slides and climbing frames are spread across the park, close to many holiday homes.</p></article>
</section>

<footer class="site-footer">
  <div class="footer-col newsletter">
    <h3>Newsletter Signup</h3>
    <p>Subscribe to hear about late deals and news from the park.</p>
    <div class="field">Enter your Name</div>
    <div class="field">Enter your Email</div>
    <span class="subscribe">Subscribe</span>
  </div>
  <div class="footer-col contact">
    <h3>Contact Information</h3>
    <p>Contact us today to book your next break or ask about availability; our friendly team is happy to help.</p>
    <div class="contact-line">
      <svg width="14" height="14" viewBox="0 0 24 24" fill="#d7e3e7"><path d="M6.6 10.8a15 15 0 0 0 6.6 6.6l2.2-2.2c.3-.3.7-.4 1-.2 1.1.4 2.3.6 3.6.6.6 0 1 .4 1 1V20c0 .6-.4 1-1 1A17 17 0 0 1 3 4c0-.6.4-1 1-1h3.5c.6 0 1 .4 1 1 0 1.3.2 2.5.6 3.6.1.3 0 .7-.2 1z"/></svg>
      <span>+44 0800 555 0142</span>
    </div>
    <div class="contact-line">
      <svg width="14" height="14" viewBox="0 0 24 24" fill="none" stroke="#d7e3e7" stroke-width="2"><rect x="3" y="5" width="18" height="14"/><path d="M3 6l9 7 9-7"/></svg>
      <span>info@pinebrookstays.com</span>
    </div>
  </div>
  <div class="footer-col sitemap">
    <h3>Sitemap</h3>
    <div class="sitemap-lists">
      <ul><li>About Us</li><li>News</li><li>Blogs</li><li>Late Deals</li><li>Holiday Homes</li><li>Local Area</li></ul>
      <ul><li>Contact Us</li><li>Reviews</li><li>Privacy Policy</li><li>Booking Terms</li><li>Offers</li><li>Site Search</li></ul>
    </div>
  </div>
</footer>

<div class="bottom-bar">
  <span>© 2015 Pinebrook Stays. All Rights Reserved</span>
  <div class="social"><span>Social Icons</span><i></i><i></i><i></i><i></i></div>
</div>

</body>
</html>
```